Thornbury Building Company - Card Design

I am looking to use the logo designs that you already did for me to develop a business card. I would like the card to have a black background and be double sided. I want white and green logo and text. I have attached an inspiration photo of a look that I like. I would like to use the Vertical Logo attached to take up the full front side of the card. On the back where I have my name and information, I would like to have the horizontal logo or maybe even just the image of the 'A' and trees without the text. I am open, but I am looking for something clean and simple and I want the green to really pop! Additional files can be found under Design #: 58302946

Target Market(s)

Homeowners

Industry/Entity Type

Construction

Contact Information for Business Card

Name: Marcus Thornbury, Title: Project Manager, Phone: 555.274.8136, Email: thornburybuildingcompany@mailvesta.com, address: 487 Larkspur Ln, Ashvale, NV 95033, Lic# 2468317

Colors
00AB8E
00BBA5
67D7C9
C6EFE9
E9F9F6

Requirements
Nice to have
• I would like to see the logos that I have already got from ArtLoomHub, though I am open to new ones

```html
<!DOCTYPE html>
<html lang="en">
<head>
<meta charset="utf-8">
<title>Thornbury Building Company – Business Card</title>
<link rel="stylesheet" href="https://fonts.googleapis.com/css2?family=Arimo:wght@400;700&display=swap">
<style>
  :root {
    --stage: #c9c9c9;
    --card: #1b1b1b;
    --green: #6db84a;
    --white: #ffffff;
  }
  * { box-sizing: border-box; margin: 0; padding: 0; }
  html, body { width: 1200px; height: 788px; overflow: hidden; }
  body {
    background: var(--stage);
    font-family: "Arimo", Arial, sans-serif;
    position: relative;
  }
  .card {
    position: absolute;
    width: 540px;
    height: 309px;
    background: var(--card);
    border-radius: 22px;
    overflow: hidden;
    box-shadow: 0 12px 28px rgba(0,0,0,.35);
  }
  .card--info { left: 40px; top: 240px; }
  .card--brand { left: 620px; top: 240px; }

  .swoosh { position: absolute; inset: 0; width: 100%; height: 100%; }

  .brand { position: absolute; display: flex; align-items: center; gap: 12px; }
  .brand__mark { background: var(--green); flex: none; }
  .brand__name {
    color: var(--white);
    font-weight: 700;
    text-transform: uppercase;
    line-height: 1.05;
  }
  .brand__name small { display: block; }
  .card--info .brand { left: 30px; top: 110px; }
  .card--info .brand__mark { width: 34px; height: 34px; }
  .card--info .brand__name { font-size: 22px; }
  .card--info .brand__name small { font-size: 11.5px; letter-spacing: .14em; margin-top: 3px; }

  .card--brand .brand { left: 50%; top: 50%; transform: translate(-50%, -50%); gap: 18px; }
  .card--brand .brand__mark { width: 62px; height: 62px; }
  .card--brand .brand__name { font-size: 44px; }
  .card--brand .brand__name small { font-size: 19px; letter-spacing: .2em; margin-top: 5px; }

  .divider {
    position: absolute;
    left: 250px; top: 44px;
    width: 1px; height: 130px;
    background: var(--green);
  }
  .contact { position: absolute; left: 268px; top: 38px; color: var(--white); }
  .contact__name { color: var(--green); font-weight: 700; font-size: 20px; text-transform: uppercase; }
  .contact__title { font-size: 12px; margin-top: 2px; }
  .contact__lic { color: var(--green); font-size: 12px; margin-top: 12px; }
  .contact__line { font-size: 11.5px; margin-top: 5px; display: flex; align-items: center; gap: 6px; }
  .contact__line svg { width: 11px; height: 11px; flex: none; }
</style>
</head>
<body>

<section class="card card--info" aria-label="Business card, contact side">
  <svg class="swoosh" viewBox="0 0 540 309" aria-hidden="true">
    <path d="M120 309 C330 296 470 262 540 196" fill="none" stroke="var(--white)" stroke-width="4"/>
    <path d="M150 309 C340 298 480 268 540 210 L540 309 Z" fill="var(--green)"/>
  </svg>

  <div class="brand">
    <span class="brand__mark"></span>
    <p class="brand__name">Thornbury<small>Building Company</small></p>
  </div>

  <div class="divider"></div>

  <div class="contact">
    <p class="contact__name">Marcus Thornbury</p>
    <p class="contact__title">Project Manager</p>
    <p class="contact__lic">Lic# 2468317</p>
    <p class="contact__line">487 Larkspur Ln, Ashvale, NV 95033</p>
    <p class="contact__line">
      <svg viewBox="0 0 12 12" aria-hidden="true"><path d="M2.5 1h2l1 3-1.3 1a6 6 0 0 0 2.8 2.8l1-1.3 3 1v2a1 1 0 0 1-1 1A9.5 9.5 0 0 1 1.5 2a1 1 0 0 1 1-1z" fill="var(--green)"/></svg>
      555.274.8136
    </p>
    <p class="contact__line">
      <svg viewBox="0 0 12 12" aria-hidden="true"><rect x="0.5" y="2" width="11" height="8" fill="var(--green)"/><path d="M0.5 2.5 6 6.5l5.5-4" fill="none" stroke="var(--card)" stroke-width="1"/></svg>
      thornburybuildingcompany@mailvesta.com
    </p>
  </div>
</section>

<section class="card card--brand" aria-label="Business card, logo side">
  <div class="brand">
    <span class="brand__mark"></span>
    <p class="brand__name">Thornbury<small>Building Company</small></p>
  </div>
</section>

</body>
</html>
```